Coll of Redwater disability insurance program

We are an endorsed vendor for disability insurance the the College of Redwater. We work together with the College to promote this program. They send emails on our behalf but we send some too. I'm not confident the emails we send are as effective as they could be. I have attached examples of 2 versions of the same email we send students and residents. I would love your opinion on how to make these better and shorter. They are emails, not brochures. I have several others but starting with these. I would like to see consistency in all the pieces we email to the students and residents. I also feel like we have to many words in our pieces and they could be shortened up with better word smithing. Once we settle on a design of these emails and better wording I have about 5 other emails I would like to have looked at to coordinate with the one we are doing now. In each of these programs at the College we have an assigned Harlan Oduya representative. We do want to add their pictures to these too as one of the examples has.
Updates

I forgot to mention that I need both logo's in the email. The Harlan Oduya logo and the College of Redwater Bureau of Learner Care Plans logo. Do you need an electronic version of the email? Let me know. Thanks

Target Market(s)

students and medical residents

Industry/Entity Type

Insurance

Font styles to use
Sans Serif

Requirements
Must have
• Short and worded to the point
• Can use maroon and gold coloring
Nice to have
• Easier to read
Should not have
• Walls of words as students and residents dont have a lot of extra time on their hands.

```html
<!DOCTYPE html>
<html lang="en">
<head>
<meta charset="utf-8">
<title>Completing Students – Disability Insurance Flyer</title>
<link rel="stylesheet" href="https://fonts.googleapis.com/css2?family=Roboto:wght@500;700&family=Source+Sans+3:wght@400;600;700&display=swap">
<style>
  :root{
    --maroon:#6e1c3b;
    --gold:#cfa935;
    --navy:#1f2f6e;
    --ink:#2b2b2b;
    --paper:#ffffff;
    --backdrop:#5b6670;
  }
  *{box-sizing:border-box;margin:0;padding:0}
  html,body{width:1200px;height:1200px;overflow:hidden;background:var(--backdrop)}
  body{font-family:"Source Sans 3",sans-serif;color:var(--ink)}
  .flyer{position:absolute;left:150px;top:18px;width:900px;height:1163px;background:var(--paper);overflow:hidden}
  .abs{position:absolute}

  /* header */
  .brand-agency{left:36px;top:44px;display:flex;align-items:center;gap:14px}
  .brand-agency .mark{width:62px;height:62px;border-radius:50%;background:var(--navy)}
  .brand-agency .name{font-family:"Source Sans 3",sans-serif;font-weight:600;font-size:40px;color:var(--navy);letter-spacing:.5px}
  .brand-college{right:36px;top:52px;display:flex;align-items:center;gap:14px}
  .brand-college .mark{width:56px;height:56px;background:var(--maroon)}
  .brand-college .name{font-weight:700;font-size:18px;line-height:1.35;color:var(--maroon)}

  /* hero */
  .hero{left:0;top:138px;width:900px;height:442px;
    background:radial-gradient(ellipse at 60% 55%,#ffffff 0%,#eef5fb 45%,#cfe0ef 100%)}
  .tag-attention{left:32px;top:470px;height:54px;padding:0 16px;background:var(--gold);
    font-family:"Roboto",sans-serif;font-weight:700;font-size:44px;line-height:54px;color:#fff}
  .tag-students{left:32px;top:524px;width:434px;height:56px;padding-left:12px;background:var(--maroon);
    font-family:"Roboto",sans-serif;font-weight:700;font-size:35px;line-height:56px;color:#fff;letter-spacing:.3px}

  /* left column */
  .intro{left:32px;top:596px;width:358px;font-size:14.5px;line-height:17.6px;text-align:justify}
  .intro h3{font-size:14.5px;font-weight:700;text-align:left}
  .intro p{margin-bottom:17px}
  .intro p.tight{margin-bottom:0}
  .intro .spacer{height:18px}

  /* benefits panel */
  .benefits{left:422px;top:590px;width:478px;height:367px;background:var(--gold)}
  .benefits h4{position:absolute;left:30px;top:8px;font-size:13.5px;font-weight:600;color:var(--ink)}
  .benefit{position:absolute;left:0;width:478px}
  .benefit .icon{position:absolute;left:-17px;top:-3px;width:34px;height:34px;border-radius:50%;
    background:var(--maroon);border:2px solid #fff;display:flex;align-items:center;justify-content:center}
  .benefit p{margin-left:30px;width:420px;font-size:13.4px;line-height:16px;color:#fff;text-align:justify}
  .benefit b{color:var(--maroon);font-weight:600}

  /* representative */
  .rep-photo{left:40px;top:979px;width:136px;height:136px;border-radius:50%;border:3px solid var(--maroon);
    background:radial-gradient(circle at 50% 40%,#c9b3a5 0%,#6d7580 55%,#3a3f46 100%)}
  .rep-signature{left:198px;top:996px}
  .rep-card{left:194px;top:1030px;font-size:14px;line-height:16px}
  .rep-card .rep-name{font-weight:600}
  .rep-card .line{display:flex;align-items:center;gap:6px}

  .legal{left:423px;top:963px;width:440px;font-size:10px;line-height:13.3px;color:#444;text-align:justify}
  .legal p{margin-bottom:7px}

  /* footer */
  .footer{left:0;top:1119px;width:900px;height:44px;background:var(--maroon);color:#fff;
    display:flex;align-items:center;justify-content:center;gap:28px;font-size:17px}
  .footer .item{display:flex;align-items:center;gap:10px}
</style>
</head>
<body>
<div class="flyer">

  <header>
    <div class="abs brand-agency">
      <span class="mark"></span>
      <span class="name">Harlan Oduya</span>
    </div>
    <div class="abs brand-college">
      <span class="mark"></span>
      <span class="name">Bureau of Learner Care Plans<br>College of Redwater</span>
    </div>
  </header>

  <div class="abs hero" role="img" aria-label="Photo of four smiling young doctors in white coats celebrating in a bright hospital hallway"></div>
  <div class="abs tag-attention">ATTENTION:</div>
  <div class="abs tag-students">COMPLETING STUDENTS</div>

  <section class="abs intro">
    <h3>Finally. It’s Your Time.</h3>
    <p>You’re close to reaping the rewards of all the hard work and sacrifices you’ve made to get where you are now.</p>
    <h3>But What Would Happen If You Became Too Sick or Injured to Work?</h3>
    <p>Even with health care costs paid by insurance, you’d still need funds for food, rent, utilities, cell phone, etc. Not only is your income essential for your daily living expenses, but also to repay student loans. Disability Income insurance (DI) can help by replacing part of your income to help you cover these critical expenses.</p>
    <div class="spacer"></div>
    <p>Take advantage of this opportunity now to obtain industry-leading coverage to protect your income and future. Don’t forget, you have access to a <b>Harborline GUARANTEED ISSUE</b> plan as a completing student!</p>
    <p class="tight">Contact your College-Designated Representative today!</p>
  </section>

  <section class="abs benefits">
    <h4>Why Consider Harborline Disability Insurance Now:</h4>

    <div class="benefit" style="top:38px">
      <span class="icon"><svg width="18" height="18" viewBox="0 0 18 18"><text x="1" y="15" font-family="Roboto,sans-serif" font-weight="700" font-size="14" fill="#fff">Aa</text></svg></span>
      <p><b>SPECIALTY LANGUAGE:</b> Coverage to protect you in your own occupation or your specialty.</p>
    </div>
    <div class="benefit" style="top:85px">
      <span class="icon"><svg width="18" height="18" viewBox="0 0 18 18" fill="none" stroke="#fff" stroke-width="1.6"><path d="M1 7l8-4 8 4-8 4z"/><path d="M4 9v4c3 2 7 2 10 0V9"/></svg></span>
      <p><b>STUDENT LOAN PROTECTION:</b> Option to cover your student loan debt.</p>
    </div>
    <div class="benefit" style="top:132px">
      <span class="icon"><svg width="18" height="18" viewBox="0 0 18 18"><path d="M9 16S1.5 11 1.5 6A3.8 3.8 0 019 4a3.8 3.8 0 017.5 2C16.5 11 9 16 9 16z" fill="#fff"/></svg></span>
      <p><b>HEALTH:</b> Your eligibility for disability insurance and your ability to obtain it on the most favorable terms depend on your health.</p>
    </div>
    <div class="benefit" style="top:179px">
      <span class="icon"><svg width="18" height="18" viewBox="0 0 18 18"><text x="4" y="15" font-family="Roboto,sans-serif" font-weight="700" font-size="16" fill="#fff">$</text></svg></span>
      <p><b>COST:</b> The cost of DI protection is age-based. Lock in a lower rate by applying while you’re young.</p>
    </div>
    <div class="benefit" style="top:227px">
      <span class="icon"><svg width="20" height="20" viewBox="0 0 20 20" fill="none" stroke="#fff" stroke-width="1.5"><circle cx="10" cy="10" r="8"/><path d="M4 16L16 4"/><text x="6.3" y="14.5" font-family="Roboto,sans-serif" font-size="12" fill="#fff" stroke="none">$</text></svg></span>
      <p><b>NO PROOF OF EARNINGS REQUIRED:</b> For eligible occupations, our Program for New Young Professionals provides a monthly benefit based on the earnings you expect early in your career - without proof of income.</p>
    </div>
    <div class="benefit" style="top:307px">
      <span class="icon"><svg width="18" height="18" viewBox="0 0 18 18"><rect x="2" y="6" width="14" height="10" rx="1.5" fill="#fff"/><path d="M6.5 6V4h5v2" fill="none" stroke="#fff" stroke-width="1.6"/></svg></span>
      <p><b>PORTABILITY:</b> You’ll likely change employers during your working life. Group LTD is typically not portable, you’ll want to consider having individual disability coverage that is with you regardless of employer.</p>
    </div>
  </section>

  <div class="abs rep-photo" role="img" aria-label="Portrait photo of the financial advisor"></div>
  <svg class="abs rep-signature" width="100" height="36" viewBox="0 0 100 36" aria-hidden="true">
    <path d="M4 30C10 14 18 6 24 8c4 2-6 20-14 22M20 20c8-2 12 2 18-2s6 2 10 0 8-8 6-2-4 10 2 6 10-6 14-4 8-2 12 0" fill="none" stroke="#222" stroke-width="1.6"/>
  </svg>
  <div class="abs rep-card">
    <div class="rep-name">Marcus T. Lindqvist</div>
    <div>Financial Advisor</div>
    <div class="line"><svg width="11" height="11" viewBox="0 0 12 12"><path d="M2.5 1l2 2.5-1 1.5c.8 1.6 1.9 2.7 3.5 3.5l1.5-1 2.5 2-1.5 1.5C5 10.5 1.5 7 1 2.5z" fill="var(--maroon)"/></svg>555-0142-0190</div>
    <div class="line"><svg width="11" height="9" viewBox="0 0 12 9"><rect width="12" height="9" fill="var(--maroon)"/><path d="M0 0l6 5 6-5" fill="none" stroke="#fff" stroke-width="1"/></svg>marcus.lindqvist@harlanoduya.com</div>
  </div>

  <section class="abs legal">
    <p>Registered Representative and Financial Advisor of Alder Row Securities LLC (ARS) 400 Mill Street, Ste 210 Redwater, 00012 (555)014-2348. Securities products/services and advisory services are offered through ARS, a registered broker/dealer and investment adviser. Financial Representative, Harborline Mutual Life Insurance Company, Eastport (Harborline). ARS is an indirect, wholly owned subsidiary of Harborline. This firm is not an affiliate or subsidiary of ARS or Harborline. ARS is a member of the Securities Dealers Board.</p>
    <p>Individual disability income products underwritten and issued by Kestrel Life Insurance Company (KLIC), Fairhaven. KLIC is a wholly owned stock subsidiary of and administrator for Harborline Mutual Life Insurance Company, Eastport or provided by Harborline. Product provisions and availability may vary by state.</p>
  </section>

  <footer class="abs footer">
    <span class="item"><svg width="16" height="16" viewBox="0 0 12 12"><path d="M2.5 1l2 2.5-1 1.5c.8 1.6 1.9 2.7 3.5 3.5l1.5-1 2.5 2-1.5 1.5C5 10.5 1.5 7 1 2.5z" fill="var(--gold)"/></svg>(555) 014-2200</span>
    <span class="item"><svg width="16" height="12" viewBox="0 0 12 9"><rect width="12" height="9" fill="var(--gold)"/><path d="M0 0l6 5 6-5" fill="none" stroke="var(--maroon)" stroke-width="1"/></svg>marcus.lindqvist@harlanoduya.com</span>
    <span class="item"><svg width="15" height="15" viewBox="0 0 16 16" fill="none" stroke="var(--gold)" stroke-width="1.4"><circle cx="8" cy="8" r="7"/><ellipse cx="8" cy="8" rx="3" ry="7"/><path d="M1 8h14"/></svg>www.redwaterdisabilitybenefits.com</span>
  </footer>

</div>
</body>
</html>
```